New Dental Office Needs an Attractive and user friendly Website Designed

I need a website for a new dental office. The Name is Harrowfield Dentistry. I would like a Modern design with a user friendly interface and usability.
I would like a landing page, a page that lists the services we offer: Cosmetic Dentistry, Implants, Dental Hygiene, Emergency Services, Restorations, Dentures
Target Market(s)
Mid to upper class
Industry/Entity Type
Dentistry
Coding
Number of Pages Required
1 page
Requirements
Must have
- Landing page that has a scheduling option, Procedures, operating hours, and contact us info
Nice to have
- Appealing design, Soft comforting colors. Easy to navigate page, Modern and professional.

```html
<!DOCTYPE html>
<html lang="en">
<head>
<meta charset="utf-8">
<title>Harrowfield Dentistry</title>
<link href="https://fonts.googleapis.com/css2?family=DM+Serif+Display&family=Figtree:wght@400;500;600;700&family=Lato:wght@400;700&family=Montserrat:wght@500;600&display=swap" rel="stylesheet">
<style>
:root{
  --blue:#1ba7ec;
  --accent:#3d8be4;
  --ink:#1e1e1e;
  --muted:#6b6b6b;
  --light:#f4f4f4;
  --dark:#231f20;
  --card-line:#d6d6d6;
  --icon-bg:#dbe8f8;
  --quote-bg:#e9f1fb;
  --star:#f6b400;
  --white:#ffffff;
}
*{margin:0;padding:0;box-sizing:border-box}
html,body{width:1200px;height:3064px;overflow:hidden;background:var(--white)}
body{position:relative;font-family:"Lato",sans-serif;color:var(--ink)}
.accent{color:var(--accent)}

/* header */
.site-header{position:absolute;left:0;top:0;width:1200px;height:90px;background:var(--white)}
.brand{position:absolute;left:140px;top:24px;font-family:"DM Serif Display",serif;font-size:30px;color:var(--ink);line-height:1.1}
.nav{position:absolute;top:38px;font-family:"Montserrat",sans-serif;font-size:13px;font-weight:500;color:var(--ink)}
.nav.active{color:var(--blue)}
.btn{position:absolute;display:flex;align-items:center;justify-content:center;gap:8px;background:var(--blue);color:var(--white);border-radius:22px;font-family:"Montserrat",sans-serif;font-weight:600;font-size:13px;text-transform:uppercase}

/* hero */
.hero-photo{position:absolute;left:0;top:90px;width:1200px;height:532px;background:linear-gradient(90deg,#f0f0f0 0%,#e4e4e4 40%,#c9c9c9 62%,#b8b8b8 80%,#a9a9a9 100%)}
.hero-title{position:absolute;left:140px;top:186px;width:520px;font-family:"DM Serif Display",serif;font-weight:400;font-size:55px;line-height:63px;color:var(--ink)}
.hero-sub{position:absolute;left:140px;top:386px;width:500px;font-family:"Montserrat",sans-serif;font-size:22px;line-height:32px;font-weight:500}

/* services */
.services{position:absolute;left:0;top:622px;width:1200px;height:623px;background:var(--light)}
.section-title{position:absolute;left:0;width:1200px;text-align:center;font-family:"Figtree",sans-serif;font-weight:600;font-size:29px}
.section-sub{position:absolute;left:0;width:1200px;text-align:center;font-size:13px;line-height:16px;color:var(--muted)}
.service-card{position:absolute;width:293px;height:174px;border:1px solid var(--card-line);border-radius:12px;background:var(--light);text-align:center}
.service-card.featured{border:2px solid var(--accent);background:var(--white)}
.service-icon{position:absolute;left:125px;top:22px;width:42px;height:42px;border-radius:50%;background:var(--icon-bg);display:flex;align-items:center;justify-content:center}
.featured .service-icon{background:var(--accent)}
.service-name{position:absolute;left:0;top:78px;width:100%;font-family:"Figtree",sans-serif;font-weight:600;font-size:20px}
.featured .service-name{color:var(--accent)}
.service-text{position:absolute;left:24px;top:108px;width:245px;font-size:12px;line-height:15.5px;color:var(--muted)}
.featured .service-text{color:var(--ink)}

/* why */
.why{position:absolute;left:0;top:1245px;width:1200px;height:401px;background:var(--dark);color:var(--white)}
.why-title{position:absolute;left:141px;top:68px;font-family:"Figtree",sans-serif;font-weight:600;font-size:29px;line-height:37px}
.why-text{position:absolute;left:141px;top:148px;width:270px;font-size:12.5px;line-height:15.5px}
.feature{position:absolute;width:290px}
.feature-head{display:flex;align-items:center;gap:13px;font-family:"Figtree",sans-serif;font-weight:500;font-size:20px}
.feature-icon{width:36px;height:36px;border-radius:50%;background:var(--icon-bg);display:flex;align-items:center;justify-content:center;flex:none}
.feature p{margin-top:10px;width:280px;font-size:12.5px;line-height:15.5px}
.feature a{display:inline-block;margin-top:14px;font-size:12.5px;color:var(--white);text-decoration:underline}

/* visit */
.map{position:absolute;left:140px;top:1833px;width:642px;height:461px;background:linear-gradient(135deg,#b9d8f5 0%,#dcdfe4 45%,#eef0e6 70%,#cfe3f6 100%)}
.visit-card{position:absolute;left:757px;top:1903px;width:301px;height:321px;background:var(--dark);border-radius:12px;color:var(--white)}
.visit-head{position:absolute;left:29px;display:flex;align-items:center;gap:7px;font-family:"Figtree",sans-serif;font-weight:500;font-size:20px}
.visit-line{position:absolute;left:29px;font-size:12.5px;line-height:15.5px}
.call-btn{position:absolute;left:29px;top:263px;width:94px;height:32px;border-radius:16px;background:var(--white);color:var(--ink);font-size:12.5px;display:flex;align-items:center;justify-content:center}

/* testimonials */
.review{position:absolute;top:2484px;width:449px;height:193px;background:var(--quote-bg);border-radius:12px}
.stars{position:absolute;left:21px;top:21px;display:flex;gap:4px}
.review-date{position:absolute;right:21px;top:26px;font-size:12.5px}
.review-text{position:absolute;left:21px;top:66px;width:400px;font-size:12.5px;line-height:15.5px}
.avatar{position:absolute;left:21px;top:114px;width:56px;height:56px;border-radius:50%;background:linear-gradient(135deg,#c9b8a0,#7d6a58)}
.review-name{position:absolute;left:91px;top:120px;font-family:"Figtree",sans-serif;font-weight:500;font-size:20px}
.review-role{position:absolute;left:91px;top:146px;font-size:12px;color:var(--muted)}
.arrow-btn{position:absolute;top:2570px;width:28px;height:28px;border-radius:4px;display:flex;align-items:center;justify-content:center}

/* footer */
.site-footer{position:absolute;left:0;top:2822px;width:1200px;height:242px;background:var(--dark);color:var(--white)}
.footer-brand{position:absolute;left:0;top:56px;width:1200px;text-align:center;font-family:"DM Serif Display",serif;font-size:25px}
.footer-nav{position:absolute;left:0;top:128px;width:1200px;display:flex;justify-content:center;gap:28px;font-size:13px}
.footer-rule{position:absolute;left:0;top:199px;width:1200px;height:1px;background:#3b3738}
.copyright{position:absolute;left:0;top:214px;width:1200px;text-align:center;font-size:11.5px}
</style>
</head>
<body>

<header class="site-header">
  <div class="brand">Harrowfield Dentistry</div>
  <span class="nav active" style="left:509px">HOME</span>
  <span class="nav" style="left:592px">SERVICES</span>
  <span class="nav" style="left:699px">CONTACT US</span>
  <div class="btn" style="left:825px;top:24px;width:233px;height:43px">
    <svg width="15" height="15" viewBox="0 0 16 16" fill="none" stroke="#fff" stroke-width="1.5"><rect x="1.5" y="3" width="13" height="11.5" rx="1.5"/><path d="M1.5 6.5h13M5 1v3M11 1v3"/></svg>
    Book an appointment
  </div>
</header>

<section>
  <div class="hero-photo" role="img" aria-label="Dentist in mask treating a smiling patient in a bright modern dental chair"></div>
  <h1 class="hero-title">Premium Dental Care for a Confident Smile</h1>
  <p class="hero-sub">Expert Cosmetic And Restorative Dentistry In A Luxurious Setting.</p>
  <div class="btn" style="left:141px;top:476px;width:233px;height:41px">
    <svg width="15" height="15" viewBox="0 0 16 16" fill="none" stroke="#fff" stroke-width="1.5"><rect x="1.5" y="3" width="13" height="11.5" rx="1.5"/><path d="M1.5 6.5h13M5 1v3M11 1v3"/></svg>
    Book an appointment
  </div>
</section>

<section class="services">
  <h2 class="section-title" style="top:56px">Our Dental <span class="accent">Services</span></h2>
  <p class="section-sub" style="top:98px">Comprehensive, high-quality care from cosmetic enhancements to<br>emergency treatments—tailored to your smile.</p>

  <div class="service-card" style="left:140px;top:170px">
    <div class="service-icon"><svg width="22" height="22" viewBox="0 0 24 24" fill="none" stroke="#3d8be4" stroke-width="1.6"><circle cx="12" cy="12" r="9"/><path d="M8 14c1 1.5 2.4 2.2 4 2.2s3-.7 4-2.2"/><circle cx="9" cy="10" r=".8" fill="#3d8be4"/><circle cx="15" cy="10" r=".8" fill="#3d8be4"/></svg></div>
    <div class="service-name">Cosmetic Dentistry</div>
    <p class="service-text">Enhance your smile with treatments that improve tooth shape, color, and appearance.</p>
  </div>
  <div class="service-card featured" style="left:454px;top:170px">
    <div class="service-icon"><svg width="22" height="22" viewBox="0 0 24 24" fill="none" stroke="#fff" stroke-width="1.6"><path d="M7 4c2-1 3.5 0 5 0s3-1 5 0 1.5 5 0 6H7C5.5 9 5 5 7 4z"/><path d="M9 10v3l3 8 3-8v-3M9 14h6M10 17h4"/></svg></div>
    <div class="service-name">Dental Implants</div>
    <p class="service-text">Permanent, natural-looking tooth replacements that restore function and confidence.</p>
  </div>
  <div class="service-card" style="left:768px;top:170px">
    <div class="service-icon"><svg width="22" height="22" viewBox="0 0 24 24" fill="none" stroke="#3d8be4" stroke-width="1.6"><path d="M5 5l14 14M19 5L5 19"/><circle cx="6" cy="6" r="2"/><circle cx="18" cy="6" r="2"/></svg></div>
    <div class="service-name">Emergency Services</div>
    <p class="service-text">Quick, professional treatment for dental emergencies, providing relief when you need it most.</p>
  </div>
  <div class="service-card" style="left:140px;top:379px">
    <div class="service-icon"><svg width="22" height="22" viewBox="0 0 24 24" fill="none" stroke="#3d8be4" stroke-width="1.6"><path d="M3 9c4 2 14 2 18 0-1 6-5 9-9 9s-8-3-9-9z"/><path d="M6 11v2M10 12v3M14 12v3M18 11v2"/></svg></div>
    <div class="service-name">Dentures</div>
    <p class="service-text">Comfortable, custom-fitted dentures that restore your smile and make eating easy again.</p>
  </div>
  <div class="service-card" style="left:454px;top:379px">
    <div class="service-icon"><svg width="22" height="22" viewBox="0 0 24 24" fill="none" stroke="#3d8be4" stroke-width="1.6"><path d="M6 4c2-1 4 .5 6 .5S16 3 18 4s1.5 7 0 9-1.5 7-3 7-1.5-5-3-5-1.5 5-3 5-1.5-5-3-7-1.5-8 0-9z"/><path d="M14 8l1 1 2-2"/></svg></div>
    <div class="service-name">Dental Hygiene</div>
    <p class="service-text">Preventive cleanings and exams to keep your teeth and gums healthy, fresh, and cavity-free.</p>
  </div>
  <div class="service-card" style="left:768px;top:379px">
    <div class="service-icon"><svg width="22" height="22" viewBox="0 0 24 24" fill="none" stroke="#3d8be4" stroke-width="1.6"><path d="M6 4c2-1 4 .5 6 .5S16 3 18 4s1.5 7 0 9-1.5 7-3 7-1.5-5-3-5-1.5 5-3 5-1.5-5-3-7-1.5-8 0-9z"/></svg></div>
    <div class="service-name">Tooth Restoration</div>
    <p class="service-text">Repair and restore damaged teeth with natural-looking fillings, crowns, and bridges for a healthier smile.</p>
  </div>
</section>

<section class="why">
  <h2 class="why-title">Why Patients<br>Choose <span class="accent">Our Clinic</span></h2>
  <p class="why-text">Experience expert care in a modern, comfort-first clinic—where advanced technology meets personalized treatment.</p>

  <div class="feature" style="left:444px;top:73px">
    <div class="feature-head"><span class="feature-icon"><svg width="18" height="18" viewBox="0 0 24 24" fill="none" stroke="#3d8be4" stroke-width="1.8"><rect x="3" y="6" width="18" height="12" rx="2"/><circle cx="12" cy="12" r="2.5"/></svg></span>Board-Certified Dentists</div>
    <p>Expertise you can trust, backed by advanced training and credentials.</p>
    <a>Learn more</a>
  </div>
  <div class="feature" style="left:765px;top:73px">
    <div class="feature-head"><span class="feature-icon"><svg width="18" height="18" viewBox="0 0 24 24" fill="none" stroke="#3d8be4" stroke-width="1.8"><path d="M6 4c2-1 4 .5 6 .5S16 3 18 4s1.5 7 0 9-1.5 7-3 7-1.5-5-3-5-1.5 5-3 5-1.5-5-3-7-1.5-8 0-9z"/></svg></span>Pain-Free Treatments</div>
    <p>Gentle techniques and modern technology for a stress-free experience.</p>
    <a>Learn more</a>
  </div>
  <div class="feature" style="left:444px;top:231px">
    <div class="feature-head"><span class="feature-icon"><svg width="18" height="18" viewBox="0 0 24 24" fill="none" stroke="#3d8be4" stroke-width="1.8"><path d="M4 19h16M7 19l3-9h6M10 10l-3-4"/><circle cx="7" cy="5" r="1.5"/></svg></span>Luxury, Comfort Clinic</div>
    <p>Designed to help you relax—because your comfort matters.</p>
    <a>Learn more</a>
  </div>
  <div class="feature" style="left:765px;top:231px">
    <div class="feature-head"><span class="feature-icon"><svg width="18" height="18" viewBox="0 0 24 24" fill="none" stroke="#3d8be4" stroke-width="1.8"><rect x="3" y="7" width="18" height="12" rx="2"/><path d="M16 13h2M6 7l9-4 2 4"/></svg></span>Flexible Payment Plans</div>
    <p>Quality care made accessible with tailored financing options.</p>
    <a>Learn more</a>
  </div>
</section>

<section>
  <h2 class="section-title" style="top:1718px">Visit Our <span class="accent">Clinic</span></h2>
  <p class="section-sub" style="top:1762px">Located in the heart of Harrowfield, our clinic offers<br>flexible hours and easy access to premium dental care.</p>
  <div class="map" role="img" aria-label="Street map showing the clinic location"></div>
  <div class="visit-card">
    <div class="visit-head" style="top:28px"><svg width="18" height="18" viewBox="0 0 24 24" fill="none" stroke="#3d8be4" stroke-width="1.8"><path d="M12 21s-7-6.5-7-12a7 7 0 0114 0c0 5.5-7 12-7 12z"/><circle cx="12" cy="9" r="2.5"/></svg>Visit Us</div>
    <p class="visit-line" style="left:37px;top:62px">48 Alder Crest Way, Harrowfield</p>
    <div class="visit-head" style="top:96px"><svg width="18" height="18" viewBox="0 0 24 24" fill="none" stroke="#3d8be4" stroke-width="1.8"><circle cx="12" cy="12" r="9"/><path d="M12 7v5l3 2"/></svg>Operating Hours</div>
    <p class="visit-line" style="top:130px">Mon–Fri: 8:00 AM – 6:00 PM<br>Sat: 9:00 AM – 2:00 PM<br>Closed Sundays</p>
    <div class="visit-head" style="top:194px"><svg width="18" height="18" viewBox="0 0 24 24" fill="none" stroke="#3d8be4" stroke-width="1.8"><path d="M5 4h4l2 5-2.5 1.5a11 11 0 005 5L15 13l5 2v4a2 2 0 01-2 2A16 16 0 013 6a2 2 0 012-2z"/></svg>Call Us</div>
    <p class="visit-line" style="top:228px">(555) 214-3086</p>
    <div class="call-btn">Call Now</div>
  </div>
</section>

<section>
  <h2 class="section-title" style="top:2366px">What Our <span class="accent">Patients Say</span></h2>
  <p class="section-sub" style="top:2410px">Real stories from patients who've experienced compassionate care,<br>outstanding results, and a confident new smile.</p>

  <div class="arrow-btn" style="left:91px;border:1.5px solid #333"><svg width="12" height="12" viewBox="0 0 12 12" fill="none" stroke="#333" stroke-width="1.6"><path d="M8 1L3 6l5 5"/></svg></div>
  <div class="arrow-btn" style="left:1080px;background:#1e1e1e"><svg width="12" height="12" viewBox="0 0 12 12" fill="none" stroke="#fff" stroke-width="1.6"><path d="M4 1l5 5-5 5"/></svg></div>

  <div class="review" style="left:140px">
    <div class="stars">
      <svg width="118" height="20" viewBox="0 0 118 20" fill="#f6b400"><g id="st"><path d="M10 1l2.6 6 6.4.5-4.9 4.2 1.5 6.3L10 14.7 4.4 18l1.5-6.3L1 7.5 7.4 7z"/></g><use href="#st" x="24"/><use href="#st" x="48"/><use href="#st" x="72"/><use href="#st" x="96"/></svg>
    </div>
    <span class="review-date">10th Feb, 2023</span>
    <p class="review-text">"The team made me feel comfortable from the moment I walked in. My smile has never looked better!"</p>
    <div class="avatar" role="img" aria-label="Patient portrait"></div>
    <div class="review-name">Owen R.</div>
    <div class="review-role">Customer</div>
  </div>
  <div class="review" style="left:610px">
    <div class="stars">
      <svg width="118" height="20" viewBox="0 0 118 20" fill="#f6b400"><use href="#st"/><use href="#st" x="24"/><use href="#st" x="48"/><use href="#st" x="72"/><use href="#st" x="96"/></svg>
    </div>
    <span class="review-date">06th Feb, 2023</span>
    <p class="review-text">"Beautiful clinic, friendly staff, and pain-free treatment. Truly a premium dental experience."</p>
    <div class="avatar" role="img" aria-label="Patient portrait" style="background:linear-gradient(135deg,#f1d36a,#c99a5a)"></div>
    <div class="review-name">Clara D.</div>
    <div class="review-role">Customer</div>
  </div>

  <div class="btn" style="left:547px;top:2727px;width:106px;height:38px;background:#4a90e2;text-transform:none;font-family:'Lato',sans-serif;font-weight:400">View All</div>
</section>

<footer class="site-footer">
  <div class="footer-brand">Harrowfield Dentistry</div>
  <nav class="footer-nav"><span>Home</span><span>Our Services</span><span>Contact Us</span></nav>
  <div class="footer-rule"></div>
  <p class="copyright">© 2025 Harrowfield Dental Care. All Rights Reserved.</p>
</footer>

</body>
</html>
```